A clean crisp business card for a Landscape Construction company. Designed to be easy to read contact/ info and also be appealing/interesting, unlike a traditional business card.

Industry/Entity Type

Landscape Construction

Contact Information for Business Card

Company name : Brambleford Landscape Construction, phone number: (877) 62Vista, website:Bramblefordyards.example, Email, sales@bramblefordyards.example

Requirements
Nice to have
• Luxurious finishes/ details…. Icons or emblems next to contact info
Should not have
• Clipart or general pictures

```html
<!DOCTYPE html>
<html lang="en">
<head>
<meta charset="utf-8">
<title>Brambleford Landscape Construction – Business Card</title>
<link rel="stylesheet" href="https://fonts.googleapis.com/css2?family=Cinzel:wght@600&family=Pathway+Gothic+One&display=swap">
<style>
  :root {
    --blue: #2b7de0;
    --blue-light: #3b9ad6;
    --green: #7edc1e;
    --green-soft: #66c46a;
    --green-deep: #58b94c;
    --ink: #111111;
    --paper: #ffffff;
    --edge: #d9d9d9;
  }
  html, body {
    margin: 0;
    padding: 0;
    width: 1200px;
    height: 750px;
    overflow: hidden;
    background: var(--paper);
  }
  .card {
    position: relative;
    width: 1200px;
    height: 750px;
    background: var(--paper);
    box-sizing: border-box;
    border: 2px solid var(--edge);
    overflow: hidden;
  }
  .side-band { position: absolute; left: 0; width: 206px; }
  .side-band--blue {
    top: 0; height: 260px;
    background: linear-gradient(180deg, var(--blue) 0%, var(--blue-light) 100%);
  }
  .side-band--green {
    top: 400px; bottom: 0;
    background: linear-gradient(180deg, var(--green-soft) 0%, var(--green-deep) 100%);
  }
  .side-name {
    position: absolute;
    left: 0; top: 300px;
    width: 206px;
    text-align: center;
    font-family: "Cinzel", serif;
    font-weight: 600;
    font-size: 20px;
    line-height: 1.2;
    color: var(--blue);
    margin: 0;
  }
  .side-name .mark {
    display: block;
    width: 26px; height: 26px;
    border-radius: 50%;
    background: var(--green);
    margin: 0 auto 8px;
  }
  .flourish-area {
    position: absolute;
    left: 90px; top: 560px;
    width: 1020px; height: 130px;
    border-radius: 65px;
    background: linear-gradient(100deg, rgba(43,125,224,0.55) 0%, rgba(126,220,30,0.6) 55%, rgba(126,220,30,0.25) 100%);
  }
  .person-name {
    position: absolute;
    left: 467px; top: 88px;
    margin: 0;
    font-family: "Pathway Gothic One", sans-serif;
    font-weight: 400;
    font-size: 44px;
    color: var(--ink);
  }
  .company {
    position: absolute;
    left: 467px; top: 272px;
    margin: 0;
    font-family: "Cinzel", serif;
    font-weight: 600;
    color: var(--blue);
    line-height: 1;
  }
  .company__name { display: block; font-size: 48px; letter-spacing: 3px; }
  .company__trade { display: block; font-size: 19px; letter-spacing: 4.5px; margin-top: 6px; }
  .contact-list {
    position: absolute;
    left: 467px; top: 362px;
    margin: 0; padding: 0;
    list-style: none;
    font-family: "Pathway Gothic One", sans-serif;
    font-size: 38px;
    color: var(--ink);
  }
  .contact-list li {
    display: flex;
    align-items: center;
    height: 53px;
  }
  .contact-list svg {
    width: 30px; height: 30px;
    margin-right: 8px;
    flex: none;
    fill: none;
    stroke: var(--ink);
    stroke-width: 1.6;
  }
</style>
</head>
<body>
<div class="card">
  <div class="side-band side-band--blue"></div>
  <p class="side-name"><span class="mark"></span>Brambleford</p>
  <div class="side-band side-band--green"></div>

  <div class="flourish-area" role="img" aria-label="Flowing green and blue swoosh ending in a leaf sprig"></div>

  <h1 class="person-name">Your name Your name</h1>

  <h2 class="company">
    <span class="company__name">Brambleford</span>
    <span class="company__trade">Landscape Construction</span>
  </h2>

  <ul class="contact-list">
    <li>
      <svg viewBox="0 0 24 24"><circle cx="12" cy="12" r="10"/><path d="M9 7 C7 9 8 13 11 16 C13 17.5 15 17.5 16 16.5 L14.5 14.5 L13 15 C11.5 14 10 12.5 9.5 11 L10.5 9.5 Z"/></svg>
      (877) 62Vista,
    </li>
    <li>
      <svg viewBox="0 0 24 24"><circle cx="12" cy="12" r="10"/><ellipse cx="12" cy="12" rx="4.5" ry="10"/><path d="M2 12 H22 M4 7 H20 M4 17 H20"/></svg>
      Bramblefordyards.example,
    </li>
    <li>
      <svg viewBox="0 0 24 24"><rect x="2" y="5" width="20" height="14"/><path d="M2 5 L12 13 L22 5 M2 19 L9 11 M22 19 L15 11"/></svg>
      sales@bramblefordyards.example
    </li>
  </ul>
</div>
</body>
</html>
```